I need a business card designed using the logo provided either vertical or horizontal......Harbourline Property Group is an Australian based real estate company that caters for the upper end of the market so the design of the business card "must reflect" the companies image!!
Colour combinations are optional but "must be realistic" and must be able to be accurately useable CMYK colours.
Please consider that any colours used "must be able to be used" and be suitable in following designs for "pull out banner signs" and "real estate signs".
The colours and the font in the attached designs are for example and other combinations are encouraged.
Target Market(s)
The High End of the Australian real estate market
Industry/Entity Type
Business
Contact Information for Business Card
Logo - Business Name - Director + Licensed Real Estate Agent - Mobile Number (Cell Phone) - Business Number - Fax - Email Address - Web address
Requirements
Must have
- Designs and colours (CMYK) that can easily be interpreted by an Australian printer.
Nice to have
- Some alternative ideas on colour and font..........the ones provided are ok and have been provided as an example but I am looking for alternative ideas
Should not have
- Loud, overly bright colours. Designs that do not reflect the professional standards of the business.
- Designs that look good on a computer monitor but can not be re-created on a printing press.............this is most important when it comes to shading etc.

```html
<!DOCTYPE html>
<html lang="en">
<head>
<meta charset="utf-8">
<title>Harbourline Property Group – Business Card</title>
<link href="https://fonts.googleapis.com/css2?family=Roboto:wght@400;500&display=swap" rel="stylesheet">
<style>
  :root {
    --backdrop: #e9e6e1;
    --card-top: #ffffff;
    --card-bottom: #d9d9d9;
    --ink: #2b2b2b;
    --ink-soft: #3a3a3a;
    --gold: #a8762a;
    --gold-light: #c9b98a;
  }
  * { margin: 0; padding: 0; box-sizing: border-box; }
  html, body {
    width: 1200px;
    height: 892px;
    overflow: hidden;
    background: var(--backdrop);
    font-family: "Roboto", Arial, sans-serif;
  }
  .canvas {
    width: 1200px;
    height: 892px;
    display: flex;
    align-items: center;
    justify-content: center;
  }
  .business-card {
    position: relative;
    width: 470px;
    height: 800px;
    background: linear-gradient(180deg, var(--card-top) 0%, var(--card-top) 35%, var(--card-bottom) 100%);
    box-shadow: 0 6px 18px rgba(0, 0, 0, 0.18);
  }
  .brand {
    position: absolute;
    top: 140px;
    left: 0;
    right: 0;
    display: flex;
    align-items: center;
    justify-content: center;
    gap: 16px;
  }
  .brand-square {
    width: 34px;
    height: 34px;
    background: var(--gold);
    flex: none;
  }
  .brand-name {
    font-weight: 500;
    font-size: 27px;
    line-height: 1.15;
    letter-spacing: 2px;
    text-transform: uppercase;
    color: var(--ink);
  }
  .person {
    position: absolute;
    top: 345px;
    left: 0;
    right: 0;
    text-align: center;
  }
  .person-name {
    font-weight: 500;
    font-size: 40px;
    color: var(--gold);
    letter-spacing: 0.5px;
  }
  .person-role {
    margin-top: 6px;
    font-weight: 400;
    font-size: 15px;
    color: var(--ink-soft);
  }
  .contact-list {
    position: absolute;
    top: 520px;
    left: 72px;
    list-style: none;
    font-weight: 400;
    font-size: 22px;
    line-height: 1.3;
    color: var(--ink);
  }
</style>
</head>
<body>
  <main class="canvas">
    <article class="business-card">
      <header class="brand">
        <span class="brand-square" aria-hidden="true"></span>
        <span class="brand-name">Harbourline<br>Property Group</span>
      </header>
      <section class="person">
        <h1 class="person-name">Employee name</h1>
        <p class="person-role">Managing Director</p>
      </section>
      <ul class="contact-list">
        <li class="contact-phone">0412 555 018</li>
        <li class="contact-web">www.harbourline.com.au</li>
        <li class="contact-email">info@harbourline.com.au</li>
        <li class="contact-street">Level 4, 18 Quayside Lane</li>
        <li class="contact-city">Harbour Bay NSW 2000</li>
      </ul>
    </article>
  </main>
</body>
</html>
```